Design and Renovation Company Luxury Business Card

I want to create a luxury business card for a Design and Renovation Firm . We will use our current logo. The company name is 528BUILDA. We do not want anything standard. We need a very unique concept.
Please see uploaded inspiration. I really like the textured paper option. I would like the card to be thick with debossing, and/or embossing options. The logo has orange in it but I would like to see the card with and without the orange. I think the orange may make the company feel less high-end. The goal is to elevate the logo not match its vibe per se of the logo. We want something very unique, not standard at all!
I would like a space for :
Logo,
Name,
Position,
Email,
Office number,
Website Address,
Business Address,
Thank you!
Have fun!
Target Market(s)
Home owners Age 35 +
Industry/Entity Type
Design and Renovation
Contact Information for Business Card
Logo, Name, Position, Email, Office number, Website Address, Business Address,.
Colors
Designer to choose colors to be used in the design.
Requirements
Must have
- A luxury designer feel. Must be black or dark grey but open to other luxury ideas.
Nice to have
- Gold, silver, black embossing or debossing. Textured paper design.
Should not have
- A cheap look and feel.

```html
<!DOCTYPE html>
<html lang="en">
<head>
<meta charset="utf-8">
<title>528BUILDA Business Card</title>
<link rel="stylesheet" href="https://fonts.googleapis.com/css2?family=Poppins:wght@400;500;600&display=swap">
<style>
  :root {
    --backdrop: #2a2a2c;
    --card: #1d1e20;
    --white: #f4f4f2;
    --gold: #d9bf86;
    --gold-deep: #b8985a;
    --rule: #55565a;
    --tile-dark: #0b0b0c;
    --tile-light: #8d8e91;
  }
  * { box-sizing: border-box; margin: 0; padding: 0; }
  html, body {
    width: 1200px; height: 1108px; overflow: hidden;
    background: var(--backdrop);
    font-family: "Poppins", sans-serif;
  }
  .canvas { position: relative; width: 1200px; height: 1108px; }
  .card {
    position: absolute;
    width: 350px; height: 570px;
    border-radius: 20px;
    background: var(--card);
    box-shadow: 0 18px 40px rgba(0,0,0,.45);
    overflow: hidden;
  }
  .card--front { left: 205px; top: 250px; }
  .card--back { left: 645px; top: 290px; }

  /* front */
  .brand {
    position: absolute; left: 0; right: 0; top: 118px;
    display: flex; flex-direction: column; align-items: center;
  }
  .brand__name {
    color: var(--white); font-weight: 500; font-size: 32px; letter-spacing: 3px; line-height: 1;
  }
  .brand__tagline {
    margin-top: 8px; color: var(--white); font-size: 10px; letter-spacing: 3.2px; font-weight: 400;
  }
  .person {
    position: absolute; left: 0; right: 0; top: 312px; text-align: center;
  }
  .person__name {
    color: var(--gold); font-weight: 600; font-size: 24px; letter-spacing: .5px; line-height: 1.1;
  }
  .person__role {
    color: var(--white); font-size: 14px; letter-spacing: .6px; line-height: 1.3;
  }
  .icon-rule {
    position: absolute; left: 42px; right: 42px; top: 382px;
    display: flex; align-items: center; gap: 10px;
  }
  .icon-rule__line { flex: 1; height: 1px; background: var(--rule); }
  .icon-rule__icons { display: flex; gap: 5px; }
  .icon {
    width: 26px; height: 26px; border-radius: 3px;
    background: linear-gradient(135deg, var(--gold), var(--gold-deep));
    display: flex; align-items: center; justify-content: center;
  }
  .contact {
    position: absolute; left: 0; right: 0; top: 420px; text-align: center;
    color: var(--white); font-size: 16px; line-height: 1.38;
  }
  .contact__accent { color: var(--gold); }
  .divider {
    position: absolute; left: 50px; right: 50px; top: 494px; height: 1px; background: var(--rule);
  }
  .address {
    position: absolute; left: 0; right: 0; top: 502px; text-align: center;
    color: var(--white); font-size: 15px; line-height: 1.35;
  }

  /* back */
  .tile-field {
    position: absolute; inset: 0;
    background: linear-gradient(160deg, var(--tile-light) 0%, #3e3f42 35%, #1a1a1c 62%, var(--tile-dark) 100%);
  }
  .back-brand {
    position: absolute; right: 40px; bottom: 120px;
    color: var(--white); font-weight: 500; font-size: 16px; letter-spacing: 2px;
  }
</style>
</head>
<body>
<main class="canvas">
  <section class="card card--front">
    <div class="brand">
      <span class="brand__name">528BUILDA</span>
      <span class="brand__tagline">Design and Renovation Firm</span>
    </div>

    <div class="person">
      <p class="person__name">ADRIAN VALCOURT</p>
      <p class="person__role">MANAGING DIRECTOR</p>
    </div>

    <div class="icon-rule">
      <span class="icon-rule__line"></span>
      <div class="icon-rule__icons">
        <span class="icon">
          <svg width="16" height="16" viewBox="0 0 24 24"><path fill="#1d1e20" d="M6.6 10.8a15 15 0 0 0 6.6 6.6l2.2-2.2c.3-.3.7-.4 1-.2 1.1.4 2.3.6 3.6.6.6 0 1 .4 1 1V20c0 .6-.4 1-1 1A17 17 0 0 1 3 4c0-.6.4-1 1-1h3.5c.6 0 1 .4 1 1 0 1.3.2 2.5.6 3.6.1.3 0 .7-.2 1z"/></svg>
        </span>
        <span class="icon">
          <svg width="16" height="16" viewBox="0 0 24 24"><rect x="3" y="6" width="18" height="12" fill="none" stroke="#1d1e20" stroke-width="2"/><path d="M3 6l9 7 9-7" fill="none" stroke="#1d1e20" stroke-width="2"/></svg>
        </span>
        <span class="icon">
          <svg width="16" height="16" viewBox="0 0 24 24"><circle cx="12" cy="12" r="9" fill="none" stroke="#1d1e20" stroke-width="2"/><ellipse cx="12" cy="12" rx="4" ry="9" fill="none" stroke="#1d1e20" stroke-width="1.6"/><path d="M3 12h18" stroke="#1d1e20" stroke-width="1.6"/></svg>
        </span>
      </div>
      <span class="icon-rule__line"></span>
    </div>

    <div class="contact">
      <p>055-274 618 903</p>
      <p>studio@528builda.com</p>
      <p>www.<span class="contact__accent">528builda</span>.com</p>
    </div>

    <span class="divider"></span>

    <div class="address">
      <p>87, Harbor Crest Avenue</p>
      <p>60318, Northvale</p>
    </div>
  </section>

  <section class="card card--back">
    <div class="tile-field" role="img" aria-label="Glossy black mosaic tile pattern fading from grey highlights at the top to deep black at the bottom"></div>
    <span class="back-brand">528BUILDA</span>
  </section>
</main>
</body>
</html>
```